Fun A1 2012 family planner using clever typography and block colour

I have been looking for an A1 2012 family planner and I have not been able to find one. Hence I would like help to develop such a planner. I plan to print it on matt paper, portrait orientated. I have attached some reference pictures of our 2011 planner. I like interesting typography, clear clean colours and simple illustration. I need space to write in daily events and need the weeks and days to be clearly delineated from each other. Each day cell needs the date and day in it (please refer to the file uploaded for a visual reference confirming this). Each weekend needs some kind of colour/ typographic delineation. I want a design for a year-at-a-view calendar. I plan to print the planner in Sydney, Australia with brightloomprints.com.au and probably to sell printed copies online. The terms & conditions of this project are that I will own the design concept 100% and in perpetuity worldwide once payment has been made. (NB. The attached Work File in Word contains a rough layout and all months, days and dates all typed up to make for quicker design.)

Target Market(s)

Reasonably well heeled family of 4. 2 parents. 2 kids. 2 pets.

Industry/Entity Type

Events

Requirements
Must have
• The calendar must be portrait (not landscape orientated), A1 size. It will be printed on matt paper by brightloomprints.com.au. It must have months running left to right (Jan-Dec) and day/date cells running top to bottom (refer 2011 planner photos in file uploaded). The day/ date cells must be around 3(w)x2(h)cm - big enough to write daily events in. Weekends must be colour/ typographically delineated. 2012 year must be noted as must "A Pebblegate Inc Project" and web address in fine print bottom left hand left hand corner.
Nice to have
• A Pebblegate Inc logo in bottom left hand corder (perhaps Nimble Owl like: http://www.artmarketly.com/design_submission.aspx?designid=731462). Header/Footer space for customisation (e.g. "Hartono-Quist 2012 Planner" or "XYZ Co 2012 Planner".
Should not have
• The calendar should not use photographs or resemble standard or cheesy wall calendars. No watermarks please.

```html
<!DOCTYPE html>
<html lang="en">
<head>
<meta charset="utf-8">
<title>2012 Year Planner</title>
<link rel="stylesheet" href="https://fonts.googleapis.com/css2?family=Nunito:wght@800&family=Roboto:wght@400&family=Roboto+Condensed:wght@300;400&display=swap">
<style>
:root{
  --ink:#7a7a7a;
  --dark:#1f1f1f;
  --paper:#ffffff;
  --paper-edge:#ececec;
  --badge:#c6dd5c;
  --jan:#f9a533;--feb:#ee6a30;--mar:#d5df24;--apr:#8dc63f;
  --may:#3bb54a;--jun:#0e9146;--jul:#1ab3e8;--aug:#1675bd;
  --sep:#ec008c;--oct:#ee3b33;--nov:#f15a29;--dec:#f7941d;
}
*{box-sizing:border-box;margin:0;padding:0}
html,body{width:847px;height:1200px;overflow:hidden}
body{background:var(--paper)}
.planner{position:relative;width:847px;height:1200px;overflow:hidden;
  background:radial-gradient(ellipse at 50% 45%,var(--paper) 55%,var(--paper-edge) 100%)}
.month{position:absolute;top:0;width:64px}
.month-name{position:absolute;top:76px;left:0;width:64px;height:64px;border-radius:50%;
  background:var(--c);color:#fff;font-family:"Nunito",sans-serif;font-weight:800;
  font-size:30px;letter-spacing:-1.5px;line-height:64px;text-align:center;white-space:nowrap}
.days{position:absolute;top:148px;left:0;width:64px;list-style:none}
.days li{width:20px;height:23px;margin:0 auto 5.69px;text-align:center;color:var(--ink);
  font-family:"Roboto Condensed",sans-serif;font-weight:300;font-size:11px;line-height:11px;padding-top:2px}
.days li small{display:block;font-size:6.5px;line-height:8px;font-weight:400;letter-spacing:.1px}
.days li.we{background:var(--c);color:#fff}
.round .days li.we{width:24px;height:24px;border-radius:50%;padding-top:3px;margin-bottom:4.69px}
.jan{--c:var(--jan);left:34px}
.feb{--c:var(--feb);left:98.6px}
.mar{--c:var(--mar);left:163.2px}
.apr{--c:var(--apr);left:227.8px}
.may{--c:var(--may);left:292.4px}
.jun{--c:var(--jun);left:357px}
.jul{--c:var(--jul);left:421.6px}
.aug{--c:var(--aug);left:486.2px}
.sep{--c:var(--sep);left:550.8px}
.oct{--c:var(--oct);left:615.4px}
.nov{--c:var(--nov);left:680px}
.dec{--c:var(--dec);left:744.6px}
.badge{position:absolute;left:-280px;top:1040px;width:560px;height:560px;border-radius:50%;background:var(--badge)}
.year{position:absolute;left:33px;top:1068px;font-family:"Roboto",sans-serif;font-weight:400;font-size:74px;letter-spacing:-2px;color:var(--dark);line-height:1}
.project{position:absolute;left:33px;top:1148px;font-family:"Roboto Condensed",sans-serif;font-weight:300;font-size:20px;letter-spacing:-.6px;color:#fff;line-height:1}
</style>
</head>
<body>
<main class="planner">

<section class="month jan round"><h2 class="month-name">Jan</h2><ol class="days">
<li class="we">01<small>SUN</small></li><li>02<small>MON</small></li><li>03<small>TUE</small></li><li>04<small>WED</small></li><li>05<small>THU</small></li><li>06<small>FRI</small></li><li class="we">07<small>SAT</small></li><li class="we">08<small>SUN</small></li><li>09<small>MON</small></li><li>10<small>TUE</small></li><li>11<small>WED</small></li><li>12<small>THU</small></li><li>13<small>FRI</small></li><li class="we">14<small>SAT</small></li><li class="we">15<small>SUN</small></li><li>16<small>MON</small></li><li>17<small>TUE</small></li><li>18<small>WED</small></li><li>19<small>THU</small></li><li>20<small>FRI</small></li><li class="we">21<small>SAT</small></li><li class="we">22<small>SUN</small></li><li>23<small>MON</small></li><li>24<small>TUE</small></li><li>25<small>WED</small></li><li>26<small>THU</small></li><li>27<small>FRI</small></li><li class="we">28<small>SAT</small></li><li class="we">29<small>SUN</small></li><li>30<small>MON</small></li><li>31<small>TUE</small></li>
</ol></section>

<section class="month feb round"><h2 class="month-name">Feb</h2><ol class="days">
<li>01<small>WED</small></li><li>02<small>THU</small></li><li>03<small>FRI</small></li><li class="we">04<small>SAT</small></li><li class="we">05<small>SUN</small></li><li>06<small>MON</small></li><li>07<small>TUE</small></li><li>08<small>WED</small></li><li>09<small>THU</small></li><li>10<small>FRI</small></li><li class="we">11<small>SAT</small></li><li class="we">12<small>SUN</small></li><li>13<small>MON</small></li><li>14<small>TUE</small></li><li>15<small>WED</small></li><li>16<small>THU</small></li><li>17<small>FRI</small></li><li class="we">18<small>SAT</small></li><li class="we">19<small>SUN</small></li><li>20<small>MON</small></li><li>21<small>TUE</small></li><li>22<small>WED</small></li><li>23<small>THU</small></li><li>24<small>FRI</small></li><li class="we">25<small>SAT</small></li><li class="we">26<small>SUN</small></li><li>27<small>MON</small></li><li>28<small>TUE</small></li><li>29<small>WED</small></li>
</ol></section>

<section class="month mar"><h2 class="month-name">Mar</h2><ol class="days">
<li>01<small>THU</small></li><li>02<small>FRI</small></li><li class="we">03<small>SAT</small></li><li class="we">04<small>SUN</small></li><li>05<small>MON</small></li><li>06<small>TUE</small></li><li>07<small>WED</small></li><li>08<small>THU</small></li><li>09<small>FRI</small></li><li class="we">10<small>SAT</small></li><li class="we">11<small>SUN</small></li><li>12<small>MON</small></li><li>13<small>TUE</small></li><li>14<small>WED</small></li><li>15<small>THU</small></li><li>16<small>FRI</small></li><li class="we">17<small>SAT</small></li><li class="we">18<small>SUN</small></li><li>19<small>MON</small></li><li>20<small>TUE</small></li><li>21<small>WED</small></li><li>22<small>THU</small></li><li>23<small>FRI</small></li><li class="we">24<small>SAT</small></li><li class="we">25<small>SUN</small></li><li>26<small>MON</small></li><li>27<small>TUE</small></li><li>28<small>WED</small></li><li>29<small>THU</small></li><li>30<small>FRI</small></li><li class="we">31<small>SAT</small></li>
</ol></section>

<section class="month apr"><h2 class="month-name">Apr</h2><ol class="days">
<li class="we">01<small>SUN</small></li><li>02<small>MON</small></li><li>03<small>TUE</small></li><li>04<small>WED</small></li><li>05<small>THU</small></li><li>06<small>FRI</small></li><li class="we">07<small>SAT</small></li><li class="we">08<small>SUN</small></li><li>09<small>MON</small></li><li>10<small>TUE</small></li><li>11<small>WED</small></li><li>12<small>THU</small></li><li>13<small>FRI</small></li><li class="we">14<small>SAT</small></li><li class="we">15<small>SUN</small></li><li>16<small>MON</small></li><li>17<small>TUE</small></li><li>18<small>WED</small></li><li>19<small>THU</small></li><li>20<small>FRI</small></li><li class="we">21<small>SAT</small></li><li class="we">22<small>SUN</small></li><li>23<small>MON</small></li><li>24<small>TUE</small></li><li>25<small>WED</small></li><li>26<small>THU</small></li><li>27<small>FRI</small></li><li class="we">28<small>SAT</small></li><li class="we">29<small>SUN</small></li><li>30<small>MON</small></li>
</ol></section>

<section class="month may"><h2 class="month-name">May</h2><ol class="days">
<li>01<small>TUE</small></li><li>02<small>WED</small></li><li>03<small>THU</small></li><li>04<small>FRI</small></li><li class="we">05<small>SAT</small></li><li class="we">06<small>SUN</small></li><li>07<small>MON</small></li><li>08<small>TUE</small></li><li>09<small>WED</small></li><li>10<small>THU</small></li><li>11<small>FRI</small></li><li class="we">12<small>SAT</small></li><li class="we">13<small>SUN</small></li><li>14<small>MON</small></li><li>15<small>TUE</small></li><li>16<small>WED</small></li><li>17<small>THU</small></li><li>18<small>FRI</small></li><li class="we">19<small>SAT</small></li><li class="we">20<small>SUN</small></li><li>21<small>MON</small></li><li>22<small>TUE</small></li><li>23<small>WED</small></li><li>24<small>THU</small></li><li>25<small>FRI</small></li><li class="we">26<small>SAT</small></li><li class="we">27<small>SUN</small></li><li>28<small>MON</small></li><li>29<small>TUE</small></li><li>30<small>WED</small></li><li>31<small>THU</small></li>
</ol></section>

<section class="month jun"><h2 class="month-name">Jun</h2><ol class="days">
<li>01<small>FRI</small></li><li class="we">02<small>SAT</small></li><li class="we">03<small>SUN</small></li><li>04<small>MON</small></li><li>05<small>TUE</small></li><li>06<small>WED</small></li><li>07<small>THU</small></li><li>08<small>FRI</small></li><li class="we">09<small>SAT</small></li><li class="we">10<small>SUN</small></li><li>11<small>MON</small></li><li>12<small>TUE</small></li><li>13<small>WED</small></li><li>14<small>THU</small></li><li>15<small>FRI</small></li><li class="we">16<small>SAT</small></li><li class="we">17<small>SUN</small></li><li>18<small>MON</small></li><li>19<small>TUE</small></li><li>20<small>WED</small></li><li>21<small>THU</small></li><li>22<small>FRI</small></li><li class="we">23<small>SAT</small></li><li class="we">24<small>SUN</small></li><li>25<small>MON</small></li><li>26<small>TUE</small></li><li>27<small>WED</small></li><li>28<small>THU</small></li><li>29<small>FRI</small></li><li class="we">30<small>SAT</small></li>
</ol></section>

<section class="month jul"><h2 class="month-name">Jul</h2><ol class="days">
<li class="we">01<small>SUN</small></li><li>02<small>MON</small></li><li>03<small>TUE</small></li><li>04<small>WED</small></li><li>05<small>THU</small></li><li>06<small>FRI</small></li><li class="we">07<small>SAT</small></li><li class="we">08<small>SUN</small></li><li>09<small>MON</small></li><li>10<small>TUE</small></li><li>11<small>WED</small></li><li>12<small>THU</small></li><li>13<small>FRI</small></li><li class="we">14<small>SAT</small></li><li class="we">15<small>SUN</small></li><li>16<small>MON</small></li><li>17<small>TUE</small></li><li>18<small>WED</small></li><li>19<small>THU</small></li><li>20<small>FRI</small></li><li class="we">21<small>SAT</small></li><li class="we">22<small>SUN</small></li><li>23<small>MON</small></li><li>24<small>TUE</small></li><li>25<small>WED</small></li><li>26<small>THU</small></li><li>27<small>FRI</small></li><li class="we">28<small>SAT</small></li><li class="we">29<small>SUN</small></li><li>30<small>MON</small></li><li>31<small>TUE</small></li>
</ol></section>

<section class="month aug"><h2 class="month-name">Aug</h2><ol class="days">
<li>01<small>WED</small></li><li>02<small>THU</small></li><li>03<small>FRI</small></li><li class="we">04<small>SAT</small></li><li class="we">05<small>SUN</small></li><li>06<small>MON</small></li><li>07<small>TUE</small></li><li>08<small>WED</small></li><li>09<small>THU</small></li><li>10<small>FRI</small></li><li class="we">11<small>SAT</small></li><li class="we">12<small>SUN</small></li><li>13<small>MON</small></li><li>14<small>TUE</small></li><li>15<small>WED</small></li><li>16<small>THU</small></li><li>17<small>FRI</small></li><li class="we">18<small>SAT</small></li><li class="we">19<small>SUN</small></li><li>20<small>MON</small></li><li>21<small>TUE</small></li><li>22<small>WED</small></li><li>23<small>THU</small></li><li>24<small>FRI</small></li><li class="we">25<small>SAT</small></li><li class="we">26<small>SUN</small></li><li>27<small>MON</small></li><li>28<small>TUE</small></li><li>29<small>WED</small></li><li>30<small>THU</small></li><li>31<small>FRI</small></li>
</ol></section>

<section class="month sep"><h2 class="month-name">Sep</h2><ol class="days">
<li class="we">01<small>SAT</small></li><li class="we">02<small>SUN</small></li><li>03<small>MON</small></li><li>04<small>TUE</small></li><li>05<small>WED</small></li><li>06<small>THU</small></li><li>07<small>FRI</small></li><li class="we">08<small>SAT</small></li><li class="we">09<small>SUN</small></li><li>10<small>MON</small></li><li>11<small>TUE</small></li><li>12<small>WED</small></li><li>13<small>THU</small></li><li>14<small>FRI</small></li><li class="we">15<small>SAT</small></li><li class="we">16<small>SUN</small></li><li>17<small>MON</small></li><li>18<small>TUE</small></li><li>19<small>WED</small></li><li>20<small>THU</small></li><li>21<small>FRI</small></li><li class="we">22<small>SAT</small></li><li class="we">23<small>SUN</small></li><li>24<small>MON</small></li><li>25<small>TUE</small></li><li>26<small>WED</small></li><li>27<small>THU</small></li><li>28<small>FRI</small></li><li class="we">29<small>SAT</small></li><li class="we">30<small>SUN</small></li>
</ol></section>

<section class="month oct"><h2 class="month-name">Oct</h2><ol class="days">
<li>01<small>MON</small></li><li>02<small>TUE</small></li><li>03<small>WED</small></li><li>04<small>THU</small></li><li>05<small>FRI</small></li><li class="we">06<small>SAT</small></li><li class="we">07<small>SUN</small></li><li>08<small>MON</small></li><li>09<small>TUE</small></li><li>10<small>WED</small></li><li>11<small>THU</small></li><li>12<small>FRI</small></li><li class="we">13<small>SAT</small></li><li class="we">14<small>SUN</small></li><li>15<small>MON</small></li><li>16<small>TUE</small></li><li>17<small>WED</small></li><li>18<small>THU</small></li><li>19<small>FRI</small></li><li class="we">20<small>SAT</small></li><li class="we">21<small>SUN</small></li><li>22<small>MON</small></li><li>23<small>TUE</small></li><li>24<small>WED</small></li><li>25<small>THU</small></li><li>26<small>FRI</small></li><li class="we">27<small>SAT</small></li><li class="we">28<small>SUN</small></li><li>29<small>MON</small></li><li>30<small>TUE</small></li><li>31<small>WED</small></li>
</ol></section>

<section class="month nov"><h2 class="month-name">Nov</h2><ol class="days">
<li>01<small>THU</small></li><li>02<small>FRI</small></li><li class="we">03<small>SAT</small></li><li class="we">04<small>SUN</small></li><li>05<small>MON</small></li><li>06<small>TUE</small></li><li>07<small>WED</small></li><li>08<small>THU</small></li><li>09<small>FRI</small></li><li class="we">10<small>SAT</small></li><li class="we">11<small>SUN</small></li><li>12<small>MON</small></li><li>13<small>TUE</small></li><li>14<small>WED</small></li><li>15<small>THU</small></li><li>16<small>FRI</small></li><li class="we">17<small>SAT</small></li><li class="we">18<small>SUN</small></li><li>19<small>MON</small></li><li>20<small>TUE</small></li><li>21<small>WED</small></li><li>22<small>THU</small></li><li>23<small>FRI</small></li><li class="we">24<small>SAT</small></li><li class="we">25<small>SUN</small></li><li>26<small>MON</small></li><li>27<small>TUE</small></li><li>28<small>WED</small></li><li>29<small>THU</small></li><li>30<small>FRI</small></li>
</ol></section>

<section class="month dec"><h2 class="month-name">Dec</h2><ol class="days">
<li class="we">01<small>SAT</small></li><li class="we">02<small>SUN</small></li><li>03<small>MON</small></li><li>04<small>TUE</small></li><li>05<small>WED</small></li><li>06<small>THU</small></li><li>07<small>FRI</small></li><li class="we">08<small>SAT</small></li><li class="we">09<small>SUN</small></li><li>10<small>MON</small></li><li>11<small>TUE</small></li><li>12<small>WED</small></li><li>13<small>THU</small></li><li>14<small>FRI</small></li><li class="we">15<small>SAT</small></li><li class="we">16<small>SUN</small></li><li>17<small>MON</small></li><li>18<small>TUE</small></li><li>19<small>WED</small></li><li>20<small>THU</small></li><li>21<small>FRI</small></li><li class="we">22<small>SAT</small></li><li class="we">23<small>SUN</small></li><li>24<small>MON</small></li><li>25<small>TUE</small></li><li>26<small>WED</small></li><li>27<small>THU</small></li><li>28<small>FRI</small></li><li class="we">29<small>SAT</small></li><li class="we">30<small>SUN</small></li><li>31<small>MON</small></li>
</ol></section>

<footer>
  <div class="badge"></div>
  <p class="year">2012</p>
  <p class="project">A Pebblegate Inc Project</p>
</footer>

</main>
</body>
</html>
```